Powerpoint Design for AI Consulting Company

Description
Velmora Quill Industries is a consulting and technology company that engineers AI transformations, automation, and decision intelligence for financial firms, mining companies, and supply chains.
We already have a logo and brand colors (see attached). We need a professional, modern PowerPoint template that reflects our brand identity and positioning.
Key Requirements
Use our logo and color palette (deep blue, orange, white/black backgrounds).
Clean, modern design with subtle technology-inspired elements (data flows, AI networks, abstract systems).
Must feel sophisticated, bold, and boardroom-ready for executive presentations.
Templates should support both dark and light backgrounds.
Deliverables
A reusable PowerPoint template (.PPTX) with at least these layouts:
Title / Cover slide – dramatic, logo placement, tagline space.
Agenda slide – clean, structured layout.
Section divider slides – strong use of brand colors.
Content slides – text + image, text + icon.
Charts & data slides – bar, line, pie, comparison table, infographics.
Case study / example project slide. - ROI / Transformation Journey
Timeline / roadmap slide.
Team profile slide.
Reframe Slide – A provocative insight that reframes the client’s current thinking.
Options & Trade-offs Slide – Matrix showing different paths and consequences.
Execution Roadmap Slide – Step-by-step phased implementation view.
Closing / thank-you slide with contact details.
Style Guide
Colors: Primary – deep blue (#0D3559), Secondary – orange (#E87722), Accents – silver/white.
Fonts: Modern sans-serif (e.g., Montserrat, Lato, or similar).
Visual elements: Abstract technology, data-inspired graphics, mathematical motifs. Avoid clutter or overly “sci-fi” looks.
Tone: Premium consulting + innovative AI firm.
Target Market(s)
Velmora Quill Industries’ target market is senior decision-makers in finance, mining, and supply chains, where complexity, risk, and ROI pressure are high. Primary buyers include family offices, boutique wealth managers, super funds, and mining/supply chain executives, who value insight-driven strategies, automation, and decision intelligence. A secondary market includes professional services (accounting, legal, medical) and regulated SMEs (daycare, aged care, community services) burdened by admin and compliance. The slide deck must appeal to a boardroom audience — authoritative, data-driven, and visually clean — while remaining flexible enough to adapt for SME professional services.
Look and feel
Each slider illustrates characteristics of the customer's brand and the style your logo design should communicate.

```html
<!DOCTYPE html>
<html lang="en">
<head>
<meta charset="utf-8">
<title>Velmora Quill Industries – Presentation Template</title>
<link href="https://fonts.googleapis.com/css2?family=Montserrat:wght@500;600;700;800&family=Lato:wght@400;700&family=Nunito+Sans:wght@400;600;700&display=swap" rel="stylesheet">
<style>
:root{
  --blue:#0B4E8C;
  --blue-deep:#0D3F73;
  --blue-dark:#083A6B;
  --orange:#E8762B;
  --paper:#F7F8FA;
  --ink:#222831;
  --muted:#4A4F57;
  --rule:#E3E6EA;
  --stage:#D6D6D8;
}
*{margin:0;padding:0;box-sizing:border-box}
html,body{width:991px;height:1200px;overflow:hidden;background:var(--stage)}
.canvas{position:relative;width:991px;height:1200px;overflow:hidden}
.slide{position:absolute;width:775px;height:436px;transform:scale(.5709);transform-origin:0 0;overflow:hidden;background:var(--paper);font-family:'Lato',sans-serif;color:var(--ink)}
.col-l{left:41.7px}.col-r{left:507.5px}
.row-1{top:52px}.row-2{top:334.6px}.row-3{top:617.2px}.row-4{top:899.8px}
.abs{position:absolute}

/* shared */
.brand{position:absolute;font-family:'Montserrat',sans-serif;font-weight:600;color:var(--blue);line-height:1.05;display:flex;align-items:center;gap:8px}
.brand-dot{width:14px;height:14px;border-radius:50%;background:var(--blue);flex:none}
.brand-small{right:40px;top:14px;font-size:14px;text-align:right}
.tab{position:absolute;left:0;top:0;width:18px;height:52px;background:var(--orange)}
.heading{position:absolute;left:38px;top:15px;font-family:'Montserrat',sans-serif;font-weight:800;font-size:25px;color:var(--blue-deep);letter-spacing:.3px}
.heading em{font-style:normal;color:var(--orange)}
.footer{position:absolute;left:0;bottom:0;width:775px;height:26px;background:var(--blue);color:#fff;font-size:9.5px;font-weight:700;display:flex}
.footer .copy{flex:1;padding-left:38px;line-height:26px}
.footer .page{width:158px;background:var(--orange);text-align:center;line-height:26px}
.photo{position:absolute;border-radius:50%}

/* cover */
.cover-brand{left:40px;top:100px;font-size:19px}
.cover-title{left:36px;top:168px;font-family:'Montserrat',sans-serif;font-weight:600;font-size:35px;line-height:41px;color:var(--blue-deep)}
.cover-title span{color:var(--orange);display:block}
.cover-rule{left:38px;top:257px;width:106px;height:3px;background:var(--orange)}
.cover-tag{left:38px;top:270px;font-size:17px;line-height:24px;color:var(--ink)}
.cover-date{left:38px;top:331px;width:135px;height:29px;border-radius:15px;background:var(--orange);color:#fff;font-family:'Montserrat',sans-serif;font-weight:600;font-size:11px;text-align:center;line-height:29px}
.cover-photo{left:400px;top:60px;width:320px;height:320px;border:9px solid var(--blue);background:radial-gradient(circle at 50% 40%,#2f8fa8 0%,#12465e 35%,#0a1c2b 75%)}

/* agenda */
.agenda-panel{left:0;top:0;width:192px;height:436px;background:var(--blue)}
.agenda-brand{left:32px;top:82px;width:140px;font-family:'Montserrat',sans-serif;font-weight:600;font-size:20px;line-height:24px;color:#fff}
.agenda-dash{left:40px;top:197px;width:34px;height:3px;background:var(--orange)}
.agenda-title{left:40px;top:205px;font-family:'Montserrat',sans-serif;font-weight:700;font-size:26px;color:#fff}
.agenda-copy{left:40px;top:398px;font-size:7.5px;color:#fff;font-family:'Montserrat',sans-serif}
.agenda-photo{left:192px;top:0;width:256px;height:436px;background:linear-gradient(160deg,#e8e2d6 0%,#b9a88f 40%,#6b5846 75%,#3f3126 100%)}
.agenda-list{left:448px;top:20px;width:327px;list-style:none}
.agenda-list li{position:relative;height:66.2px;border-bottom:1px solid var(--rule);padding-left:32px;line-height:66px;font-family:'Montserrat',sans-serif;font-weight:700;font-size:13.5px;color:var(--ink)}
.agenda-list li:last-child{border-bottom:none}
.agenda-list .num{position:absolute;left:-17px;top:16px;width:34px;height:34px;border-radius:50%;background:var(--orange);border:3px solid #fff;box-shadow:0 0 0 1px #f3d2bb;color:#fff;font-size:14px;line-height:28px;text-align:center}

/* about */
.about-text{left:38px;top:62px;width:342px;font-size:11px;line-height:19.7px;color:var(--ink)}
.about-text p+p{margin-top:19.7px}
.about-photo{left:497px;top:89px;width:286px;height:286px;border:8px solid #DFE6EE;background:radial-gradient(circle at 45% 45%,#6c7c88 0%,#2f3b46 45%,#12181e 85%)}

/* what we do */
.step{position:absolute;width:126px;text-align:center}
.step h3{font-family:'Montserrat',sans-serif;font-weight:700;font-size:12.5px;color:var(--ink);margin-bottom:8px;white-space:nowrap}
.step p{font-size:8.4px;line-height:16.5px;color:var(--muted)}

/* intro */
.intro{background:radial-gradient(ellipse at 20% 10%,#0E5A9C 0%,var(--blue) 45%,var(--blue-dark) 100%)}
.intro-brand{left:0;top:128px;width:775px;text-align:center;font-family:'Montserrat',sans-serif;font-weight:600;font-size:30px;color:#fff}
.intro-title{left:0;top:205px;width:775px;text-align:center;font-family:'Montserrat',sans-serif;font-weight:800;font-size:39px;color:#fff;letter-spacing:.5px}
.intro-rule{left:343px;top:272px;width:89px;height:3px;background:#fff}
.intro-sub{left:0;top:290px;width:775px;text-align:center;font-family:'Nunito Sans',sans-serif;font-size:23px;color:#fff}

/* services */
.svc-label{position:absolute;font-size:12px;color:var(--ink);font-family:'Nunito Sans',sans-serif;line-height:14px}
.svc-center{left:266px;top:118px;width:220px;height:220px;border-radius:50%;border:3px solid var(--blue);background:#fff;display:flex;align-items:center;justify-content:center;text-align:center;font-family:'Montserrat',sans-serif;font-weight:600;font-size:21px;line-height:26px;color:var(--blue)}

/* timeline */
.tl-text{position:absolute;width:160px;text-align:center;font-size:7.8px;line-height:13.5px;color:var(--muted)}
.tl-q{position:absolute;width:60px;text-align:center;font-family:'Montserrat',sans-serif;font-weight:600;font-size:13px;color:var(--ink)}

/* closing */
.close-brand{left:40px;top:100px;font-size:19px}
.close-title{left:35px;top:166px;font-family:'Montserrat',sans-serif;font-weight:700;font-size:33px;color:var(--blue-deep)}
.close-rule{left:37px;top:214px;width:115px;height:2px;background:var(--orange)}
.close-sub{left:37px;top:226px;font-family:'Montserrat',sans-serif;font-weight:600;font-size:21px;color:var(--orange)}
.contact{position:absolute;left:38px;display:flex;align-items:center;gap:12px;font-size:12px;color:var(--ink)}
.contact b{font-family:'Montserrat',sans-serif;font-weight:700}
.contact-icon{width:28px;height:28px;border-radius:50%;background:var(--orange);display:flex;align-items:center;justify-content:center}
.close-photo{left:420px;top:50px;width:336px;height:336px;border:9px solid var(--blue);background:linear-gradient(135deg,#2d3a44 0%,#3c4b52 40%,#6a5a4e 60%,#263038 100%)}
</style>
</head>
<body>
<div class="canvas">

  <!-- Cover -->
  <section class="slide col-l row-1 cover">
    <div class="brand cover-brand"><span class="brand-dot"></span><span>VELMORA QUILL<br>INDUSTRIES</span></div>
    <h1 class="abs cover-title">VELMORA QUILL<span>INDUSTRIES</span></h1>
    <div class="abs cover-rule"></div>
    <p class="abs cover-tag">AI Transformation | Automation |<br>Decision Intelligence</p>
    <div class="abs cover-date">XX AUGUST 2025</div>
    <div class="photo cover-photo" role="img" aria-label="Hand touching a glowing AI chip interface"></div>
  </section>

  <!-- Agenda -->
  <section class="slide col-r row-1 agenda" style="background:#fff">
    <div class="abs agenda-panel"></div>
    <div class="abs agenda-brand">VELMORA QUILL INDUSTRIES</div>
    <div class="abs agenda-dash"></div>
    <h2 class="abs agenda-title">AGENDA</h2>
    <p class="abs agenda-copy">© 2024 . ALL RIGHTS RESERVED.</p>
    <div class="abs agenda-photo" role="img" aria-label="Smiling woman working on a laptop by a window"></div>
    <ol class="abs agenda-list">
      <li><span class="num">1</span>INTRODUCTION</li>
      <li><span class="num">2</span>ABOUT US</li>
      <li><span class="num">3</span>WELCOME MESSAGE</li>
      <li><span class="num">4</span>OUR SERVICES</li>
      <li><span class="num">5</span>GRAPH/CHART</li>
      <li><span class="num">6</span>CONTACT US</li>
    </ol>
  </section>

  <!-- About -->
  <section class="slide col-l row-2 about">
    <div class="tab"></div>
    <h2 class="heading">ABOUT <em>US</em></h2>
    <div class="brand brand-small">VELMORA QUILL<br>INDUSTRIES</div>
    <div class="abs about-text">
      <p>Lorem ipsum dolor sit amet, consectetur adipiscing elit, sed do eiusmod tempor incididunt ut labore et dolore magna aliqua. Ut enim ad minim veniam, quis nostrud exercitation ullamco laboris nisi ut aliquip ex ea commodo consequat. Duis aute irure dolor in reprehenderit in voluptate velit esse cillum dolore eu fugiat nulla pariatur.</p>
      <p>Excepteur sint occaecat cupidatat non proident, sunt in culpa qui officia deserunt mollit anim id est laborum.Sed ut perspiciatis unde omnis iste natus error sit voluptatem accusantium doloremque laudantium, totam rem aperiam, eaque ipsa quae ab illo inventore veritatis et quasi architecto beatae vitae dicta sunt explicabo.Nemo enim ipsam voluptatem quia voluptas sit aspernatur aut odit aut fugit, sed quia consequuntur magni dolores eos qui ratione voluptatem sequi nesciunt.</p>
    </div>
    <div class="photo about-photo" role="img" aria-label="Businessman using an AI assistant dashboard on a laptop"></div>
    <div class="footer"><span class="copy">Copyrights@2025.Company Name.All Rights Reserved</span><span class="page">Page Number 03</span></div>
  </section>

  <!-- What we do -->
  <section class="slide col-r row-2 process">
    <div class="tab"></div>
    <h2 class="heading">WHAT <em>WE DO</em></h2>
    <div class="brand brand-small">VELMORA QUILL<br>INDUSTRIES</div>
    <svg class="abs" style="left:0;top:0" width="775" height="436" viewBox="0 0 775 436" aria-hidden="true">
      <defs>
        <g id="step-top">
          <path d="M182,135V107H38V297H135" fill="none" stroke="var(--orange)" stroke-width="3.5"/>
          <path d="M132,289L145,297L132,305Z" fill="var(--orange)"/>
        </g>
        <g id="step-bottom">
          <path d="M275,150H175V345H320V315" fill="none" stroke="var(--blue)" stroke-width="3.5"/>
          <path d="M272,142L285,150L272,158Z" fill="var(--blue)"/>
        </g>
      </defs>
      <use href="#step-top"/><use href="#step-bottom"/>
      <use href="#step-top" x="276"/><use href="#step-bottom" x="276"/>
      <use href="#step-top" x="552"/>
      <g font-family="Montserrat,sans-serif" font-weight="600" font-size="14" text-anchor="middle">
        <circle cx="110" cy="107" r="13" fill="#fff" stroke="var(--orange)" stroke-width="3"/><text x="110" y="112" fill="var(--orange)">1</text>
        <circle cx="247" cy="345" r="13" fill="#fff" stroke="var(--blue)" stroke-width="3"/><text x="247" y="350" fill="var(--blue)">2</text>
        <circle cx="386" cy="107" r="13" fill="#fff" stroke="var(--orange)" stroke-width="3"/><text x="386" y="112" fill="var(--orange)">3</text>
        <circle cx="523" cy="345" r="13" fill="#fff" stroke="var(--blue)" stroke-width="3"/><text x="523" y="350" fill="var(--blue)">4</text>
        <circle cx="662" cy="107" r="13" fill="#fff" stroke="var(--orange)" stroke-width="3"/><text x="662" y="112" fill="var(--orange)">5</text>
      </g>
    </svg>
    <div class="step" style="left:47px;top:137px"><h3>Our Experience</h3><p>We bring years of experience, drawn from across the widest range of healthcare challenges, in imagining, designing and implementing digital and transformational change.</p></div>
    <div class="step" style="left:184px;top:180px"><h3>Our Impact</h3><p>We are focused, efficient and connected, enabling rapid and sustainable progress</p></div>
    <div class="step" style="left:323px;top:137px"><h3>Our Connections</h3><p>We are connected to a wide range of focused experts and partners, meaning we just do what we are good at.</p></div>
    <div class="step" style="left:460px;top:180px"><h3>Our Team</h3><p>We are built from trust and relationships, having worked together across many years and projects</p></div>
    <div class="step" style="left:599px;top:137px"><h3>Our Choice</h3><p>We don't have to do this, but this is what we enjoy!</p></div>
    <div class="footer"><span class="copy">Copyrights@2025.Company Name.All Rights Reserved</span><span class="page">Page Number 04</span></div>
  </section>

  <!-- Section divider -->
  <section class="slide col-l row-3 intro">
    <div class="abs intro-brand">VELMORA QUILL INDUSTRIES</div>
    <h2 class="abs intro-title">INTRODUCTION</h2>
    <div class="abs intro-rule"></div>
    <p class="abs intro-sub">Sustainable energy solutions</p>
  </section>

  <!-- Services -->
  <section class="slide col-r row-3 services">
    <div class="tab"></div>
    <h2 class="heading">OUR <em>SERVICES</em></h2>
    <div class="brand brand-small">VELMORA QUILL<br>INDUSTRIES</div>
    <div class="abs svc-center">VELMORA<br>QUILL<br>INDUSTRIES</div>
    <svg class="abs" style="left:0;top:0" width="775" height="436" viewBox="0 0 775 436" aria-hidden="true">
      <defs>
        <g id="person-icon" fill="none" stroke="#fff" stroke-width="1.6">
          <circle cx="0" cy="-5" r="4.5"/>
          <path d="M-9,10C-9,3-5,0,0,0S9,3,9,10"/>
          <rect x="-12" y="-13" width="24" height="26" rx="3" stroke-width="1.1"/>
        </g>
      </defs>
      <g>
        <circle cx="263" cy="120" r="25" fill="var(--orange)"/><use href="#person-icon" x="263" y="120"/>
        <circle cx="233" cy="183" r="25" fill="var(--blue)"/><use href="#person-icon" x="233" y="183"/>
        <circle cx="229" cy="259" r="25" fill="var(--orange)"/><use href="#person-icon" x="229" y="259"/>
        <circle cx="258" cy="325" r="25" fill="var(--blue)"/><use href="#person-icon" x="258" y="325"/>
        <circle cx="493" cy="120" r="25" fill="var(--blue)"/><use href="#person-icon" x="493" y="120"/>
        <circle cx="523" cy="183" r="25" fill="var(--orange)"/><use href="#person-icon" x="523" y="183"/>
        <circle cx="530" cy="259" r="25" fill="var(--blue)"/><use href="#person-icon" x="530" y="259"/>
        <circle cx="499" cy="325" r="25" fill="var(--orange)"/><use href="#person-icon" x="499" y="325"/>
      </g>
    </svg>
    <span class="svc-label" style="right:544px;top:113px">Patients</span>
    <span class="svc-label" style="right:574px;top:176px">GPs</span>
    <span class="svc-label" style="right:578px;top:252px">Specialists</span>
    <span class="svc-label" style="right:549px;top:318px">Carers</span>
    <span class="svc-label" style="left:528px;top:113px">Employees</span>
    <span class="svc-label" style="left:558px;top:176px">Influencers</span>
    <span class="svc-label" style="left:565px;top:252px">Policy makers</span>
    <span class="svc-label" style="left:534px;top:318px">Public</span>
    <div class="footer"><span class="copy">Copyrights@2025.Company Name.All Rights Reserved</span><span class="page">Page Number 06</span></div>
  </section>

  <!-- Timeline -->
  <section class="slide col-l row-4 timeline">
    <div class="tab"></div>
    <h2 class="heading">TIMELINE</h2>
    <div class="brand brand-small">VELMORA QUILL<br>INDUSTRIES</div>
    <svg class="abs" style="left:0;top:0" width="775" height="436" viewBox="0 0 775 436" aria-hidden="true">
      <circle cx="37" cy="212" r="2.5" fill="var(--blue)"/>
      <circle cx="733" cy="212" r="2.5" fill="var(--orange)"/>
      <g font-family="Montserrat,sans-serif" font-weight="600" font-size="14" fill="#fff" text-anchor="middle">
        <circle cx="117" cy="211" r="27" fill="var(--blue)"/><text x="117" y="216">2016</text>
        <circle cx="230" cy="211" r="27" fill="var(--orange)"/><text x="230" y="216">2022</text>
        <circle cx="335" cy="211" r="27" fill="var(--blue)"/><text x="335" y="216">2023</text>
        <circle cx="434" cy="212" r="27" fill="var(--orange)"/><text x="434" y="217">2023</text>
        <circle cx="535" cy="211" r="27" fill="var(--blue)"/><text x="535" y="216">2024</text>
        <circle cx="644" cy="212" r="27" fill="var(--orange)"/><text x="644" y="217">2024</text>
      </g>
    </svg>
    <p class="tl-text" style="left:42px;top:138px;width:150px">Lorem ipsum dolor sit amet, consectetur adipiscing elit, sed</p>
    <p class="tl-text" style="left:257px;top:104px">Lorem ipsum dolor sit amet, consectetur adipiscing elit, sed do eiusmod tempor incididunt ut labore et dolore magna aliqua.</p>
    <span class="tl-q" style="left:305px;top:156px">Q1</span>
    <p class="tl-text" style="left:450px;top:97px">Lorem ipsum dolor sit amet, consectetur adipiscing elit, sed do eiusmod tempor incididunt ut labore et dolore magna aliqua.</p>
    <span class="tl-q" style="left:505px;top:156px">Q3</span>
    <p class="tl-text" style="left:150px;top:252px">Lorem ipsum dolor sit amet, consectetur adipiscing elit, sed do eiusmod tempor incididunt ut labore et dolore magna aliqua.</p>
    <span class="tl-q" style="left:404px;top:250px">Q2</span>
    <p class="tl-text" style="left:354px;top:270px">Lorem ipsum dolor sit amet, consectetur adipiscing elit, sed do eiusmod tempor incididunt ut labore et dolore magna aliqua.</p>
    <span class="tl-q" style="left:614px;top:250px">Q4</span>
    <p class="tl-text" style="left:564px;top:270px">Lorem ipsum dolor sit amet, consectetur adipiscing elit, sed do eiusmod tempor incididunt ut labore et dolore magna aliqua.</p>
    <div class="footer"><span class="copy">Copyrights@2025.Company Name.All Rights Reserved</span><span class="page">Page Number 07</span></div>
  </section>

  <!-- Closing -->
  <section class="slide col-r row-4 closing">
    <div class="brand close-brand"><span class="brand-dot"></span><span>VELMORA QUILL<br>INDUSTRIES</span></div>
    <h2 class="abs close-title">THANK YOU</h2>
    <div class="abs close-rule"></div>
    <h3 class="abs close-sub">CONTACT US</h3>
    <div class="contact" style="top:270px">
      <span class="contact-icon"><svg width="14" height="14" viewBox="0 0 24 24" aria-hidden="true"><path fill="#fff" d="M6.6 10.8a15.1 15.1 0 0 0 6.6 6.6l2.2-2.2c.3-.3.7-.4 1-.2 1.1.4 2.3.6 3.6.6.6 0 1 .4 1 1V20c0 .6-.4 1-1 1A17 17 0 0 1 3 4c0-.6.4-1 1-1h3.5c.6 0 1 .4 1 1 0 1.3.2 2.5.6 3.6.1.3 0 .7-.2 1z"/></svg></span>
      <span><b>PHONE:</b>&nbsp; +1 555 0142 7788</span>
    </div>
    <div class="contact" style="top:318px">
      <span class="contact-icon"><svg width="14" height="14" viewBox="0 0 24 24" aria-hidden="true"><path fill="#fff" d="M3 5h18c.6 0 1 .4 1 1v12c0 .6-.4 1-1 1H3c-.6 0-1-.4-1-1V6c0-.6.4-1 1-1zm9 7 8.5-5.3H3.5z"/></svg></span>
      <span><b>EMAIL:</b>&nbsp; info@velmoraquill.com</span>
    </div>
    <div class="photo close-photo" role="img" aria-label="Aerial view of a cargo plane beside a container ship at port"></div>
  </section>

</div>
</body>
</html>
```